Commercial, Public Works, Contractor needs a modern web design

We are a General and Engineering contracting firm with vast experience in our industry. Our focus is on Commercial, Tenant Improvement, Restaurants, and Public Works. We are opening a new business and would like that excitement and energy to show through the new web design. The colors we like are black, red and grey, we are open to color ideas. Attached is our logo design.

Industry/Entity Type

Restaurant

```html
<!DOCTYPE html>
<html lang="en">
<head>
<meta charset="utf-8">
<title>Korvan Build, Inc. — General Engineering Contracting Firm</title>
<link href="https://fonts.googleapis.com/css2?family=Roboto+Condensed:wght@400;700&family=Arimo:wght@400&display=swap" rel="stylesheet">
<style>
:root{
  --page:#1a1a1a;
  --panel:#232323;
  --panel-dark:#1f1f1f;
  --nav:#262626;
  --line:#353535;
  --red:#c41a16;
  --red-dark:#8e0d0b;
  --orange:#e5532a;
  --white:#ffffff;
  --text:#cfcfcf;
  --muted:#9a9a9a;
  --dim:#6d6d6d;
}
*{box-sizing:border-box;margin:0;padding:0}
html,body{width:1073px;height:1200px;overflow:hidden;background:var(--page)}
body{position:relative;font-family:"Roboto Condensed",sans-serif;color:var(--text)}
.abs{position:absolute}

/* header */
.brand{left:89px;top:22px;display:flex;align-items:center;gap:8px}
.brand-mark{width:40px;height:40px;border-radius:50%;background:var(--red)}
.brand-name{font-size:17px;font-weight:700;color:var(--red);letter-spacing:.5px;line-height:1}
.contact{top:54px;text-align:right;font-size:11px;color:var(--white);line-height:1.3}
.contact small{display:block;font-size:8px;color:var(--muted)}
.contact-icon{top:55px;width:26px;height:26px;border-radius:50%;background:var(--red);display:flex;align-items:center;justify-content:center}
.search{left:762px;top:54px;width:223px;height:29px;background:var(--panel);border:1px solid var(--line);display:flex;align-items:center}
.search span{flex:1;padding-left:15px;font-size:10px;color:var(--muted)}
.search i{width:28px;height:100%;border-left:1px solid var(--line);display:flex;align-items:center;justify-content:center}

/* nav */
.nav{left:89px;top:114px;width:897px;height:44px;display:flex;background:var(--nav)}
.nav a{flex:1;display:flex;align-items:center;padding-left:18px;font-size:11px;color:var(--muted);text-decoration:none;border-right:1px solid var(--page)}
.nav a:last-child{border-right:0}
.nav a.active{background:linear-gradient(var(--red),var(--red-dark));color:var(--white)}

/* hero */
.hero{left:89px;top:158px;width:897px;height:403px;background:linear-gradient(100deg,#3c4245 0%,#2c3133 45%,#4a4f52 70%,#2b2f31 100%)}
.hero-title{left:121px;top:308px;font-size:29px;color:var(--orange);white-space:nowrap;font-weight:400}
.hero-title span{font-size:17px;color:var(--white)}
.hero-sub{left:120px;top:352px;font-size:19.5px;line-height:29px;color:var(--white)}
.hero-arrows{left:122px;top:421px;display:flex;gap:2px}
.hero-arrows i{width:22px;height:22px;background:var(--red);display:flex;align-items:center;justify-content:center}

/* focus cards */
.section-title{font-size:15.5px;color:var(--white);font-weight:400}
.card{top:622px;width:214px;height:156px}
.card-img{height:124px}
.card-label{height:32px;background:linear-gradient(var(--red),var(--red-dark));color:var(--white);font-size:12.5px;display:flex;align-items:center;padding-left:12px}

/* about + news */
.about-text{left:89px;top:849px;width:575px;font-family:"Arimo",sans-serif;font-size:9px;line-height:20.8px;color:var(--muted)}
.news-arrows{left:962px;top:821px;display:flex;gap:6px}
.news{left:698px;top:852px;width:287px;height:110px;background:var(--panel);padding:19px 22px}
.news h3{font-weight:400;font-size:10.5px;color:var(--text)}
.news em{display:block;font-family:"Arimo",sans-serif;font-size:8px;color:var(--dim);margin-top:6px}
.news p{font-family:"Arimo",sans-serif;font-size:9px;line-height:20.8px;color:var(--muted);margin-top:3px}

/* partners */
.partners{left:89px;top:996px;width:897px;height:70px;background:var(--panel);display:flex;align-items:center;justify-content:space-around;padding:0 24px}
.partners span{font-size:19px;color:#7f7f7f;display:flex;align-items:center;gap:6px}
.partners b{width:12px;height:12px;border-radius:50%;background:#7f7f7f;display:inline-block}

/* footer */
.footer{left:89px;top:1094px;width:897px;height:66px;background:var(--panel-dark)}
.footer-links{left:29px;top:26px;display:flex;gap:18px;font-size:9px;color:var(--text)}
.footer-links em{font-style:normal;color:var(--dim)}
.copyright{left:29px;top:54px;font-size:8.5px;color:var(--text)}
.follow{left:648px;top:40px;display:flex;align-items:center;gap:17px;font-size:9px;color:var(--text)}
.follow i{width:13px;height:13px;border-radius:50%;background:#8a8a8a;display:inline-block}
</style>
</head>
<body>

<header>
  <div class="abs brand"><span class="brand-mark"></span><span class="brand-name">KORVAN BUILD, INC.</span></div>

  <div class="abs contact" style="left:470px;width:109px"><small>CALL US</small>info@korvanbuild.com</div>
  <div class="abs contact-icon" style="left:592px">
    <svg width="12" height="9" viewBox="0 0 12 9"><rect x=".5" y=".5" width="11" height="8" rx="1" fill="#fff"/><path d="M1 1l5 4 5-4" stroke="#c41a16" fill="none"/></svg>
  </div>
  <div class="abs contact" style="left:614px;width:90px"><small>CALL US</small>( 2103 ) 555 018</div>
  <div class="abs contact-icon" style="left:716px">
    <svg width="13" height="13" viewBox="0 0 24 24"><path fill="#fff" d="M6.6 10.8a15 15 0 006.6 6.6l2.2-2.2c.3-.3.7-.4 1-.2 1.1.4 2.3.6 3.6.6.6 0 1 .4 1 1V20c0 .6-.4 1-1 1A17 17 0 013 4c0-.6.4-1 1-1h3.5c.6 0 1 .4 1 1 0 1.3.2 2.5.6 3.6.1.3 0 .7-.2 1z"/></svg>
  </div>

  <div class="abs search"><span>SEARCH</span><i>
    <svg width="11" height="11" viewBox="0 0 11 11"><circle cx="4.5" cy="4.5" r="3.5" stroke="#777" fill="none" stroke-width="1.3"/><path d="M7 7l3 3" stroke="#777" stroke-width="1.3"/></svg></i></div>
</header>

<nav class="abs nav">
  <a class="active" href="#">ABOUT US</a><a href="#">SERVICES</a><a href="#">SUPPORT</a><a href="#">NEWS</a><a href="#">CONTACT US</a>
</nav>

<section>
  <div class="abs hero" role="img" aria-label="Engineer in an orange hard hat and high-visibility jacket standing before heavy machinery"></div>
  <h1 class="abs hero-title">GENERAL ENGINEERING <span>CONTRACTING FIRM</span></h1>
  <p class="abs hero-sub">OUR FOCUS IS ON COMMERCIAL,TENANT IMPROVEMENT,<br>RESTAURANTS, AND PUBLIC WORKS.</p>
  <div class="abs hero-arrows">
    <i><svg width="7" height="11" viewBox="0 0 7 11"><path d="M6 1L1.5 5.5 6 10" stroke="#fff" fill="none" stroke-width="1.3"/></svg></i>
    <i><svg width="7" height="11" viewBox="0 0 7 11"><path d="M1 1l4.5 4.5L1 10" stroke="#fff" fill="none" stroke-width="1.3"/></svg></i>
  </div>
</section>

<section>
  <h2 class="abs section-title" style="left:90px;top:583px">GENERAL ENGINEERING CONTRACTING FIRM FOCUSING ON</h2>
  <div class="abs card" style="left:89px"><div class="card-img" role="img" aria-label="Glass skyscrapers seen from below" style="background:linear-gradient(#8a8a8a,#3a3a3a)"></div><div class="card-label">COMMERCIAL</div></div>
  <div class="abs card" style="left:317px"><div class="card-img" role="img" aria-label="Businessman walking toward a sunlit city skyline" style="background:radial-gradient(circle at 75% 40%,#e8dcb0,#7d7458 55%,#3e3b30)"></div><div class="card-label">TENANT IMPROVEMENT</div></div>
  <div class="abs card" style="left:544px"><div class="card-img" role="img" aria-label="Modern restaurant dining room with warm lighting" style="background:linear-gradient(#3b2a1f,#2a2523 60%,#8c8580)"></div><div class="card-label">RESTAURANTS</div></div>
  <div class="abs card" style="left:772px"><div class="card-img" role="img" aria-label="Construction workers tying steel rebar cages" style="background:linear-gradient(#8d8a86,#6b5a4e)"></div><div class="card-label">PUBLIC WORKS</div></div>
</section>

<section>
  <h2 class="abs section-title" style="left:90px;top:817px">ABOUT GENERAL ENGINEERING</h2>
  <p class="abs about-text">Lorem Ipsum is simply dummy text of the printing and typesetting industry. Lorem Ipsum has been the industry's standard dummy text ever since the 1500s, when an unknown printer took a galley of type and scrambled it to make a type specimen book. It has survived not only five centuries, but also the leap into electronic typesetting, remaining essentially unchanged. It was popularised in the 1960s with the release of Pressline sheets containing Lorem Ipsum passages, and more recently with desktop publishing software like Quillset Layout including versions of Lorem Ipsum.</p>

  <h2 class="abs section-title" style="left:695px;top:817px">LATEST NEWS</h2>
  <div class="abs news-arrows">
    <svg width="6" height="9" viewBox="0 0 6 9"><path d="M5 1L1.5 4.5 5 8" stroke="#aaa" fill="none"/></svg>
    <svg width="6" height="9" viewBox="0 0 6 9"><path d="M1 1l3.5 3.5L1 8" stroke="#aaa" fill="none"/></svg>
  </div>
  <article class="abs news">
    <h3>LOREM IPSUM IS SIMPLY DUMMY TEXT OF THE PRINTING</h3>
    <em>Posted on 27 November 2014</em>
    <p>Lorem Ipsum has been the industry's standard dummy text ever since the 1500s, when an unknown printer...</p>
  </article>
</section>

<div class="abs partners">
  <span>Zorvenal</span><span>Trelmiqa</span><span><b></b>Oskavin</span><span>Brunmerel</span><span>Yldrasque</span><span><b></b>Calvenmoor</span>
</div>

<footer class="abs footer">
  <div class="abs footer-links"><span>HOME</span><em>/</em><span>ABOUT US</span><em>/</em><span>SERVICES</span><em>/</em><span>SUPPORT</span><em>/</em><span>NEWS</span><em>/</em><span>CONTACT US</span></div>
  <p class="abs copyright">COPYRIGHT 2015, GENERAL ENGINEERING CONTRACTING FIRM. ALL RIGHTS RESERVED.</p>
  <div class="abs follow"><span>FOLLOW US :</span><i aria-label="Social profile"></i><i aria-label="Social profile"></i><i aria-label="Social profile"></i><i aria-label="Social profile"></i><i aria-label="Social profile"></i><i aria-label="News feed"></i></div>
</footer>

</body>
</html>
```